Wilderness Doc & TV personality personal page

I’m a wilderness and EMS emergency physician with particular sub specialties and a TV show. I need a website to highlight my interviews, teachings, etc... I did buy a number of domains for now.
Topics and things I need: CV (or version) me in the media, picture gallery, actually I sort of really like what dr owen barkley, my colleague has setup plus I have tv show and stuff like that. ridgeway healer dot com

Target Market(s)

EMS, education, commercial products...

Industry/Entity Type

Medical And Science

Coding

Coded - Design and coding required

Number of Pages Required

1 page

Font styles to use
Sans Serif

Colors
f37122
9bcb3c
0556a4
a54499

Requirements
Must have
• Links and photos to news articles and things that mention me that I can add in.
Nice to have
• Maybe some snapshots of lecture reviews or patient thank you notes. Accolades so to speak
• I really appreciate how sharp it is. I would love to see Headings that resemble my friend's at ridgeway healer dot com. Home, experience, consulting, lectures, affiliates, contact... those are main subjects... I think media also and that will have the TV show stuff and articles written about me...then maybe at the bottom of main page also have splits for training, research, television, and maybe exploration
Should not have
• The medical symbol with two snakes... that means quack doctor

```html
<!DOCTYPE html>
<html lang="en">
<head>
<meta charset="utf-8">
<title>Julian Marsh — Wilderness &amp; EMS Physician</title>
<link href="https://fonts.googleapis.com/css2?family=Lato:wght@400;700;900&display=swap" rel="stylesheet">
<style>
:root{
  --ink:#1f1f1f;
  --body:#3a3a3a;
  --brand-blue:#0d4aa0;
  --deep-blue:#1a4a9c;
  --purple:#a0358f;
  --green:#8cc63f;
  --rule:#dcdcdc;
  --footer:#2b2b2b;
  --white:#ffffff;
}
*{margin:0;padding:0;box-sizing:border-box}
html,body{width:1200px;height:2862px;overflow:hidden;background:var(--white)}
body{position:relative;font-family:'Lato',sans-serif;color:var(--ink)}
.abs{position:absolute}

/* header */
.site-header{left:0;top:0;width:1200px;height:96px;background:var(--white)}
.logo{left:74px;top:31px;font-weight:900;font-size:33px;color:var(--brand-blue);letter-spacing:.5px}
.main-nav{left:367px;top:42px;display:flex;gap:0;width:760px;justify-content:space-between;font-size:14.5px;font-weight:700;text-transform:uppercase}
.main-nav a{color:var(--ink);text-decoration:none}
.main-nav a.active{color:var(--purple)}

/* hero */
.hero{left:0;top:96px;width:1200px;height:594px;background:linear-gradient(90deg,#d8b3b6 0%,#e3c9c6 30%,#b9c7c8 48%,#6f8f5a 62%,#2f6f8a 75%,#4c7a3c 100%)}
.hero-copy{left:74px;top:250px}
.hero-kicker{font-size:28px;font-weight:700;color:var(--ink)}
.hero-title{font-size:57px;font-weight:900;color:var(--ink);line-height:1;margin-top:4px}
.hero-lede{font-size:25px;font-weight:700;color:var(--brand-blue);line-height:37px;margin-top:10px;width:480px}
.btn{display:inline-block;font-weight:700;font-size:17px;color:var(--white);text-transform:uppercase;text-align:center;text-decoration:none}
.btn-purple{background:var(--purple)}
.btn-green{background:var(--green)}
.hero-btn{left:74px;top:477px;width:180px;height:53px;line-height:53px}

/* about */
.about-photo{left:103px;top:757px;width:356px;height:356px;border-radius:50%;background:radial-gradient(circle at 40% 35%,#f1f1f1 0%,#c9cc4a 45%,#2d3a2a 100%)}
.about-copy{left:524px;top:768px;width:605px}
.section-title{font-size:29px;font-weight:900;text-transform:uppercase;color:var(--ink)}
.about-creds{font-size:22px;font-weight:900;color:var(--brand-blue);margin-top:8px}
.about-text{font-size:16.5px;line-height:31.3px;color:var(--body);margin-top:14px}
.about-btn{left:524px;top:1040px;width:180px;height:53px;line-height:53px}
.divider{left:74px;top:1174px;width:1052px;height:1px;background:var(--rule)}

/* interview + tv */
.interview{left:74px;top:1220px;width:332px;height:407px;background:var(--deep-blue)}
.interview-title{position:absolute;left:0;top:26px;width:100%;text-align:center;color:var(--white);font-size:29px;font-weight:900;line-height:31px;text-transform:uppercase}
.interview-media{position:absolute;left:15px;top:110px;width:302px;height:280px;background:linear-gradient(135deg,#3d4b6b,#1e8c8c 55%,#24305a)}
.play{position:absolute;width:52px;height:52px}
.tv-title{left:434px;top:1213px}
.carousel-arrows{left:1084px;top:1220px;width:44px;height:22px}
.show-card{top:1271px;width:333px}
.show-thumb{position:relative;width:333px;height:196px}
.show-name{font-size:19px;font-weight:700;color:var(--purple);text-transform:uppercase;margin-top:22px}
.show-text{font-size:16.5px;line-height:25.6px;color:var(--body);margin-top:6px}
.watch{display:block;font-size:15px;font-weight:900;color:var(--green);text-transform:uppercase;margin-top:14px;text-decoration:none}

/* media band */
.media-band{left:0;top:1681px;width:1200px;height:515px;background:linear-gradient(100deg,#8f2b8c 0%,#5a3590 45%,#1446a0 100%)}
.media-copy{left:74px;top:1785px;width:620px;color:var(--white)}
.media-copy .section-title{color:var(--white)}
.media-text{font-size:16.5px;line-height:31.3px;margin-top:18px;color:#f0ecf6}
.media-btn{left:74px;top:2028px;width:180px;height:53px;line-height:53px}
.media-photo{left:742px;top:1760px;width:356px;height:356px;border-radius:50%;background:radial-gradient(circle at 50% 40%,#cfd2cc 0%,#6d7a5a 50%,#2a2f2a 100%)}

/* gallery */
.gallery-title{left:0;top:2249px;width:1200px;text-align:center}
.shot{height:178px}

/* footer */
.site-footer{left:0;top:2741px;width:1200px;height:121px;background:var(--footer)}
.footer-nav{left:74px;top:2778px;display:flex;gap:34px;font-size:13px;font-weight:700;text-transform:uppercase}
.footer-nav a{color:var(--white);text-decoration:none}
.copyright{left:74px;top:2807px;font-size:12px;color:#d6d6d6}
.social{left:954px;top:2797px;display:flex;gap:20px}
.social span{display:block;width:20px;height:20px;border-radius:50%;background:#cfcfcf}
</style>
</head>
<body>

<header class="abs site-header">
  <div class="abs logo">JULES MARSH</div>
  <nav class="abs main-nav">
    <a class="active" href="#">Home</a>
    <a href="#">About Us</a>
    <a href="#">TV Shows</a>
    <a href="#">Interviews</a>
    <a href="#">Services</a>
    <a href="#">Gallery</a>
    <a href="#">Contact Us</a>
  </nav>
</header>

<section class="abs hero" role="img" aria-label="Photo of the physician in blue scrubs with arms crossed, standing by a waterfront with a city skyline"></section>
<div class="abs hero-copy">
  <div class="hero-kicker">WELCOME TO</div>
  <h1 class="hero-title">JULIAN MARSH</h1>
  <p class="hero-lede">I’m a wilderness and EMS emergency physician&nbsp; with particular sub specialties and a TV show.</p>
</div>
<a class="abs btn btn-purple hero-btn" href="#">Read More</a>

<div class="abs about-photo" role="img" aria-label="Portrait of the physician in a white fire rescue uniform beside an emergency vehicle"></div>
<div class="abs about-copy">
  <h2 class="section-title">About Julian Marsh</h2>
  <div class="about-creds">DO, EMT-P, FAWM</div>
  <p class="about-text">Julian Marsh, DO, EMT-P, FAWM, is an assistant professor of emergency medicine and EMS at the Coastal State University. He’s an active EMS physician with multiple departments in Florida, including medical director for Harbor County Fire Rescue Task Force Two USAR and very active globally in wilderness/austere EMS.</p>
</div>
<a class="abs btn btn-green about-btn" href="#">Read More</a>
<div class="abs divider"></div>

<section class="abs interview">
  <h3 class="interview-title">Interview with<br>Julian Marsh</h3>
  <div class="interview-media" role="img" aria-label="Video still of the physician in scrubs in front of a colourful mural">
    <svg class="play" style="left:125px;top:114px" viewBox="0 0 52 52"><circle cx="26" cy="26" r="26" fill="#fff"/><path d="M20 15 L37 26 L20 37 Z" fill="#1a2b4f"/></svg>
  </div>
</section>

<h2 class="abs section-title tv-title">TV Shows</h2>
<svg class="abs carousel-arrows" viewBox="0 0 44 22"><path d="M9 3 L3 11 L9 19" fill="none" stroke="#888" stroke-width="2"/><path d="M35 3 L41 11 L35 19" fill="none" stroke="#888" stroke-width="2"/></svg>

<article class="abs show-card" style="left:434px">
  <div class="show-thumb" role="img" aria-label="Video still of the physician outdoors in front of an old stone gate" style="background:linear-gradient(135deg,#6f7a55,#3d5b7a 55%,#8b8f80)">
    <svg class="play" style="left:140px;top:72px" viewBox="0 0 52 52"><circle cx="26" cy="26" r="26" fill="#fff"/><path d="M20 15 L37 26 L20 37 Z" fill="#1f1f1f"/></svg>
  </div>
  <h4 class="show-name">Fusce at vestibulum</h4>
  <p class="show-text">Quisque euismod lobortis felis, ac tincidunt neque porta interdum accumsan sceleri sque vitae id ligula..</p>
  <a class="watch" href="#">Watch Video</a>
</article>

<article class="abs show-card" style="left:793px">
  <div class="show-thumb" role="img" aria-label="Video still of a panel discussion at a conference table" style="background:linear-gradient(180deg,#7a5a40,#3a3530 55%,#1f4a32)">
    <svg class="play" style="left:140px;top:72px" viewBox="0 0 52 52"><circle cx="26" cy="26" r="26" fill="#fff"/><path d="M20 15 L37 26 L20 37 Z" fill="#1f1f1f"/></svg>
  </div>
  <h4 class="show-name">Fusce at vestibulum</h4>
  <p class="show-text">Quisque euismod lobortis felis, ac tincidunt neque porta interdum accumsan sceleri sque vitae id ligula..</p>
  <a class="watch" href="#">Watch Video</a>
</article>

<section class="abs media-band"></section>
<div class="abs media-copy">
  <h2 class="section-title">About Me in Media</h2>
  <p class="media-text">Julian Marsh, DO, EMT-P, FAWM, is an assistant professor of emergency medicine and EMS at the Coastal State University. He’s an active EMS physician with multiple departments in Florida, including medical director for Harbor County Fire Rescue Task Force Two USAR and very active globally in wilderness/austere EMS.</p>
</div>
<a class="abs btn btn-green media-btn" href="#">Read More</a>
<div class="abs media-photo" role="img" aria-label="Group photo of four people posing with raised arms in front of an outdoor sign"></div>

<h2 class="abs section-title gallery-title">Gallery</h2>
<div class="abs shot" style="left:74px;top:2313px;width:252px;background:linear-gradient(135deg,#6b5a48,#2e3a4a)" role="img" aria-label="Two responders in sunglasses outdoors"></div>
<div class="abs shot" style="left:341px;top:2313px;width:251px;background:linear-gradient(135deg,#c9c2b8,#3a4a8a)" role="img" aria-label="Family celebrating a graduation"></div>
<div class="abs shot" style="left:609px;top:2313px;width:251px;background:linear-gradient(180deg,#e6e2dc,#3a3530)" role="img" aria-label="Team standing by a mobile medical unit"></div>
<div class="abs shot" style="left:876px;top:2313px;width:250px;background:linear-gradient(135deg,#cfc8c2,#3d5a7a)" role="img" aria-label="Physician examining a patient"></div>
<div class="abs shot" style="left:74px;top:2506px;width:340px;background:linear-gradient(180deg,#8a6a48,#2a2622 60%,#1f4a32)" role="img" aria-label="Panel speakers at a conference table"></div>
<div class="abs shot" style="left:431px;top:2506px;width:340px;background:linear-gradient(180deg,#a07a5a,#d8d2c8 60%,#8a7a6a)" role="img" aria-label="Group of responders in matching shirts"></div>
<div class="abs shot" style="left:787px;top:2506px;width:339px;background:linear-gradient(135deg,#1f7a4a,#142a22 55%,#3a2a3a)" role="img" aria-label="Physician lecturing on stage"></div>

<footer class="abs site-footer"></footer>
<nav class="abs footer-nav">
  <a href="#">Home</a><a href="#">About Us</a><a href="#">TV Shows</a><a href="#">Interviews</a><a href="#">Services</a><a href="#">Gallery</a><a href="#">Contact Us</a>
</nav>
<div class="abs copyright">Copyright © 2019 .Company Name. All Right Reserved</div>
<div class="abs social" aria-label="Social links">
  <span></span><span></span><span></span><span></span><span></span>
</div>

</body>
</html>
```